Kestrelbrook Student Accomodation needs a business card design

Hi Guys,

We are a Student Accommodation company in Australia. We already have a logo which I will submit.

I will require the design of the business cards from you.

I am after something that looks clean, modern and that people feel interested and actually want to contact us.

We would like to see designs that are innovative.

On the business cards I will require to have:

Employee Name
Position
Phone number
Email
Facebook page

I hope you can help me with this project guys as I have heard really good things from you.

```html
<!DOCTYPE html>
<html lang="en">
<head>
<meta charset="utf-8">
<title>Kestrelbrook Student Accomodation – Business Card</title>
<link rel="stylesheet" href="https://fonts.googleapis.com/css2?family=Open+Sans:wght@400;700&family=Oswald:wght@500&display=swap">
<style>
  :root {
    --green: #16873d;
    --yellow: #f7c031;
    --gold: #e7a92b;
    --ink: #2b2b2b;
    --paper: #ffffff;
    --backdrop: #ece7df;
  }
  * { margin: 0; padding: 0; box-sizing: border-box; }
  html, body { width: 1200px; height: 765px; overflow: hidden; }
  body {
    background: var(--backdrop);
    font-family: "Open Sans", Arial, sans-serif;
    position: relative;
  }
  .card {
    position: absolute;
    width: 598px;
    height: 342px;
    background: var(--paper);
    box-shadow: 0 4px 14px rgba(0,0,0,.18);
    overflow: hidden;
  }
  .card--front { left: 103px; top: 51px; z-index: 2; }
  .card--back { left: 518px; top: 360px; z-index: 1; }

  .top-band { position: absolute; left: 0; top: 0; width: 598px; height: 70px; }

  .brand {
    position: absolute;
    display: flex;
    align-items: center;
    gap: 12px;
  }
  .brand__mark { background: var(--yellow); flex: none; }
  .brand__name {
    font-family: "Oswald", "Arial Narrow", sans-serif;
    font-weight: 500;
    color: var(--green);
    letter-spacing: 1px;
    line-height: 1;
  }
  .card--front .brand { left: 0; right: 0; top: 138px; justify-content: center; }
  .card--front .brand__mark { width: 34px; height: 34px; }
  .card--front .brand__name { font-size: 36px; }
  .card--back .brand { left: 0; right: 0; top: 140px; justify-content: center; }
  .card--back .brand__mark { width: 52px; height: 52px; }
  .card--back .brand__name { font-size: 54px; }

  .person {
    position: absolute;
    right: 382px;
    top: 258px;
    text-align: right;
  }
  .person__name { font-size: 21px; font-weight: 700; color: var(--green); line-height: 1.2; }
  .person__role { font-size: 17px; color: var(--yellow); line-height: 1.3; }

  .divider {
    position: absolute;
    left: 259px;
    top: 244px;
    width: 2px;
    height: 82px;
    background: linear-gradient(var(--yellow), var(--gold));
  }

  .contacts {
    position: absolute;
    left: 273px;
    top: 245px;
    list-style: none;
  }
  .contacts li {
    display: flex;
    align-items: center;
    gap: 8px;
    font-size: 16px;
    color: var(--ink);
    height: 27.5px;
  }
  .contacts svg { width: 13px; height: 13px; flex: none; }
</style>
</head>
<body>

<section class="card card--front" aria-label="Business card front">
  <svg class="top-band" viewBox="0 0 598 70" aria-hidden="true">
    <path d="M0 0 H598 V2 Q299 110 0 2 Z" fill="var(--green)"/>
    <path d="M0 0 H598 Q299 104 0 0 Z" fill="var(--yellow)"/>
  </svg>

  <div class="brand">
    <span class="brand__mark"></span>
    <span class="brand__name">KESTRELBROOK</span>
  </div>

  <div class="person">
    <p class="person__name">Employee Name</p>
    <p class="person__role">Position</p>
  </div>

  <span class="divider"></span>

  <ul class="contacts">
    <li>
      <svg viewBox="0 0 24 24" aria-hidden="true"><path fill="var(--ink)" d="M6.6 10.8a15.1 15.1 0 0 0 6.6 6.6l2.2-2.2c.3-.3.7-.4 1-.2 1.1.4 2.3.6 3.6.6.6 0 1 .4 1 1V20c0 .6-.4 1-1 1A17 17 0 0 1 3 4c0-.6.4-1 1-1h3.5c.6 0 1 .4 1 1 0 1.3.2 2.5.6 3.6.1.3 0 .7-.2 1z"/></svg>
      <span>123-456-7890</span>
    </li>
    <li>
      <svg viewBox="0 0 24 24" aria-hidden="true"><path fill="var(--green)" d="M2 5h20v14H2z"/><path d="M2 5l10 8 10-8" fill="none" stroke="#fff" stroke-width="2"/></svg>
      <span>info@kestrelbrook.com</span>
    </li>
    <li>
      <svg viewBox="0 0 24 24" aria-hidden="true"><rect x="2" y="2" width="20" height="20" rx="2" fill="var(--green)"/></svg>
      <span>/kestrelbrookstudents</span>
    </li>
  </ul>
</section>

<section class="card card--back" aria-label="Business card back">
  <div class="brand">
    <span class="brand__mark"></span>
    <span class="brand__name">KESTRELBROOK</span>
  </div>
</section>

</body>
</html>
```